Organization and people consulting firm needs a website design

I need a website that promotes and explains the consulting service we will provide. The organization is called Bluefinch Advisory Partners. Our services include organization design, employee experience, change management, and executive coaching. I would like to see a simple clean and professional design, that reflects a modern and forward looking professional services company

Target Market(s)

Mid market and large companies

Industry/Entity Type

Management Consulting

Coding

Coded - Design and coding required

Number of Pages Required

5+ page

Font styles to use
Sans Serif

Colors

Designer to choose colors to be used in the design.

Requirements
Must have
• The following pages: Home, The Way We Work, What We Do, Our Founder, Insights, Contact.
• Search button.
• Hyper links (will be provided with main body text)
• Scrolling website with summaries at top level and links to more detail at lower level (like this website: veltracore.com)
• Company logo (uploaded)
• I have text for each of the pages that I can upload once the basic design is done
Should not have
• No clutter, keep the design clean

```html
<!DOCTYPE html>
<html lang="en">
<head>
<meta charset="utf-8">
<title>Bluefinch Advisory Partners</title>
<link rel="stylesheet" href="https://fonts.googleapis.com/css2?family=Lato:ital,wght@0,400;0,700;0,900;1,400&display=swap">
<style>
:root{
  --red:#d4002a;
  --red-soft:#f3c9cf;
  --ink:#2b2b2b;
  --text:#444;
  --grey-band:#eeeeee;
  --dark:#3a3a3a;
  --black:#120708;
  --white:#fff;
}
*{box-sizing:border-box;margin:0;padding:0}
html,body{width:1200px;height:3435px;overflow:hidden}
body{font-family:'Lato',sans-serif;color:var(--text);background:var(--white);position:relative}
.abs{position:absolute}
.center{text-align:center}

/* header */
.site-header{position:absolute;top:0;left:0;width:1200px;height:115px;background:var(--white);display:flex;align-items:center;padding:0 78px}
.brand{display:flex;align-items:center;gap:12px;font-size:30px;font-weight:700;color:var(--red);width:250px}
.brand-dot{width:22px;height:22px;border-radius:50%;background:var(--red)}
.main-nav{display:flex;gap:36px;margin-left:28px;font-size:14px;font-weight:700;color:var(--ink)}
.main-nav .active{color:var(--red)}
.search{margin-left:auto;width:150px;height:34px;border:1px solid #ccc;border-radius:17px;display:flex;align-items:center;justify-content:space-between;padding:0 3px 0 14px;font-size:12px;color:#555}
.search-btn{width:28px;height:28px;border-radius:50%;background:#666}

/* hero */
.hero{top:115px;left:0;width:1200px;height:545px;background:linear-gradient(120deg,#4b5460 0%,#9aa3ad 35%,#c9cdd2 55%,#6d6a6c 80%,#2f2d30 100%)}
.hero-title{top:190px;width:1200px;color:var(--white);font-size:38px;font-weight:700;line-height:46px;letter-spacing:1px}
.hero-sub{top:297px;width:1200px;color:var(--white);font-size:24px;font-style:italic}
.hero-dots{top:498px;left:568px;display:flex;gap:9px}
.hero-dots span{width:10px;height:10px;border-radius:50%;background:var(--white)}
.hero-dots span:first-child{background:var(--red)}

/* sections */
.section-mark{width:16px;height:16px;border-radius:50%;background:var(--red);left:592px}
.section-title{width:1200px;font-size:26px;font-weight:900;color:var(--ink);letter-spacing:.5px}
.body-copy{font-size:14.5px;line-height:27px;color:var(--text)}
.btn{height:44px;border-radius:22px;background:var(--red);color:var(--white);font-size:14px;font-weight:700;display:flex;align-items:center;justify-content:center}

/* services */
.service{width:243px;height:258px;top:1290px;text-align:center;padding-top:28px;border-radius:26px}
.service.featured{background:var(--white);box-shadow:0 4px 14px rgba(0,0,0,.18)}
.service svg{width:54px;height:50px}
.service h3{color:var(--red);font-size:14.5px;font-weight:700;margin:20px 0 10px}
.service p{font-size:14px;line-height:25px;padding:0 22px}

/* founder */
.founder-photo{left:717px;top:1805px;width:306px;height:306px;border-radius:50%;background:radial-gradient(circle at 45% 40%,#e9eef3 0%,#aebfd0 55%,#5a7796 100%);border:4px solid #d9e2ea}

/* insights */
.insight{top:2466px;width:330px;height:225px;background:var(--white);border-radius:24px;padding:32px 22px}
.insight h3{color:var(--red);font-size:17px;font-weight:700}
.insight .date{font-size:15px;font-weight:700;color:var(--ink);margin:10px 0 8px}
.insight p{font-size:14px;line-height:23px}
.insight a{display:inline-block;margin-top:14px;font-size:14px;color:var(--red);text-decoration:underline}

/* contact */
.contact-line{width:1200px;font-size:14px;display:flex;justify-content:center;align-items:center;gap:14px}
.contact-line svg{width:14px;height:14px;fill:var(--red)}

/* footer */
.copyright{top:3343px;width:1200px;color:var(--white);font-size:11px}
.social{top:3376px;left:508px;display:flex;gap:16px}
.social span{width:20px;height:20px;border-radius:50%;background:var(--white)}
</style>
</head>
<body>

<header class="site-header">
  <div class="brand"><span class="brand-dot"></span>Bluefinch</div>
  <nav class="main-nav">
    <span class="active">HOME</span><span>THE WAY WE WORK</span><span>WHAT WE DO</span><span>OUR FOUNDER</span><span>INSIGHTS</span><span>CONTACT</span>
  </nav>
  <div class="search">Search..<span class="search-btn"></span></div>
</header>

<section class="hero abs" role="img" aria-label="Photo of consultants meeting around a boardroom table"></section>
<h1 class="hero-title abs center" style="top:305px">WELCOME TO<br>BLUEFINCH ADVISORY PARTNERS</h1>
<p class="hero-sub abs center" style="top:405px">We are organisation &amp; people consulting firm</p>
<div class="hero-dots abs" style="top:613px"><span></span><span></span><span></span><span></span></div>

<!-- background bands -->
<svg class="abs" style="top:660px;left:0" width="1200" height="2775" viewBox="0 0 1200 2775">
  <defs>
    <linearGradient id="insightsGrad" x1="0" x2="1" y1="0" y2="0">
      <stop offset="0" stop-color="#0d0405"/>
      <stop offset=".55" stop-color="#5a0712"/>
      <stop offset="1" stop-color="#d4002a"/>
    </linearGradient>
  </defs>
  <path d="M0 210 C300 420 700 520 1200 290 L1200 900 C850 1000 380 980 0 800 Z" fill="var(--grey-band)"/>
  <path d="M600 1180 C760 1070 950 1050 1090 1090 C1010 1160 950 1230 900 1340 Z" fill="var(--red-soft)" opacity=".6"/>
  <path d="M0 1420 C380 1650 800 1600 1200 1430 L1200 2000 C950 2200 450 2180 0 1920 Z" fill="url(#insightsGrad)"/>
  <path d="M0 2500 C300 2690 700 2700 1200 2550 L1200 2775 L0 2775 Z" fill="var(--dark)"/>
</svg>

<!-- the way we work -->
<span class="section-mark abs" style="top:720px"></span>
<h2 class="section-title abs center" style="top:750px">THE WAY WE WORK</h2>
<p class="body-copy abs center" style="top:796px;left:170px;width:860px">Aliquam molestie, mi et imperdiet euismod, dui purus auctor tellus, et interdum lacus lectus et ante. Sed accumsan sollicitudin sapien, sit amet adipiscing turpis gravida ac. In congue, neque ac lobortis volutpat, libero mauris varius mi, vitae suscipit ipsum ligula vitae risus. Duis aliquam nibh a dui iaculis viverra id a velit. Vivamus egestas risus in magna varius commodo. Sed semper viverra egestas. Etiam pretium porttitor lectus, vel ornare neque porta volutpat.</p>
<div class="btn abs" style="top:938px;left:510px;width:180px">READ MORE</div>

<!-- what we do -->
<span class="section-mark abs" style="top:1148px"></span>
<h2 class="section-title abs center" style="top:1178px">WHAT WE DO</h2>
<p class="body-copy abs center" style="top:1226px;width:1200px">Aliquam molestie, mi et imperdiet euismod, dui purus auctor tellus, et interdum lacus lectus et ante.</p>

<div class="service featured abs" style="left:76px">
  <svg viewBox="0 0 54 50" fill="#333"><rect x="19" y="2" width="16" height="12"/><rect x="2" y="34" width="14" height="12"/><rect x="20" y="34" width="14" height="12"/><rect x="38" y="34" width="14" height="12"/><rect x="26" y="14" width="2" height="10"/><rect x="8" y="23" width="38" height="2"/><rect x="8" y="23" width="2" height="11"/><rect x="26" y="23" width="2" height="11"/><rect x="44" y="23" width="2" height="11"/></svg>
  <h3>ORGANISATION DESIGN</h3><p>Aliquam molestie, mi et imperdiet euismod, dui purus auctor tellus, et interdum lacus lectus et ante..</p>
</div>
<div class="service abs" style="left:344px">
  <svg viewBox="0 0 54 50" fill="#333"><circle cx="27" cy="14" r="8"/><circle cx="11" cy="18" r="6"/><circle cx="43" cy="18" r="6"/><path d="M13 46 C13 30 41 30 41 46 Z"/><path d="M1 44 C1 30 18 28 18 34 L14 44 Z"/><path d="M53 44 C53 30 36 28 36 34 L40 44 Z"/></svg>
  <h3>EMPLOYEE EXPERIENCE</h3><p>Aliquam molestie, mi et imperdiet euismod, dui purus auctor tellus, et interdum lacus lectus et ante..</p>
</div>
<div class="service abs" style="left:616px">
  <svg viewBox="0 0 54 50" fill="#333"><circle cx="17" cy="12" r="8"/><circle cx="37" cy="30" r="7"/><path d="M5 40 C5 24 29 24 29 40 Z"/><path d="M25 49 C25 38 49 38 49 49 Z"/><path d="M34 4 L46 4 L46 16 L42 12 L36 18 L32 14 L38 8 Z"/></svg>
  <h3>CHANGE MANAGEMENT</h3><p>Aliquam molestie, mi et imperdiet euismod, dui purus auctor tellus, et interdum lacus lectus et ante..</p>
</div>
<div class="service abs" style="left:889px">
  <svg viewBox="0 0 54 50" fill="#333"><rect x="16" y="2" width="36" height="24" fill="none" stroke="#333" stroke-width="2"/><path d="M20 22 L28 14 L34 18 L46 8" fill="none" stroke="#333" stroke-width="2"/><circle cx="9" cy="16" r="6"/><path d="M1 34 C1 22 17 22 17 34 Z"/><rect x="0" y="36" width="54" height="3"/><circle cx="18" cy="42" r="3"/><circle cx="30" cy="42" r="3"/><circle cx="42" cy="42" r="3"/></svg>
  <h3>EXECUTIVE COACHING</h3><p>Aliquam molestie, mi et imperdiet euismod, dui purus auctor tellus, et interdum lacus lectus et ante..</p>
</div>

<!-- our founder -->
<span class="section-mark abs" style="top:1770px;left:361px"></span>
<h2 class="section-title abs center" style="top:1812px;left:-230px">OUR FOUNDER</h2>
<h3 class="abs center" style="top:1860px;left:75px;width:590px;color:var(--red);font-size:19px;font-weight:700">NAME HEADING</h3>
<p class="abs center" style="top:1893px;left:75px;width:590px;font-size:14px;font-weight:700;color:var(--ink)">(Founder of Bluefinch Advisory Partners)</p>
<p class="body-copy abs center" style="top:1917px;left:75px;width:590px">Aliquam molestie, mi et imperdiet euismod, dui purus auctor tellus, et interdum lacus lectus et ante. Sed accumsan sollicitudin sapien, sit amet adipiscing turpis gravida ac. In congue, neque ac lobortis volutpat, libero mauris varius mi, vitae suscipit ipsum ligula vitae risus. Duis aliquam nibh a dui iaculis viverra id a velit.</p>
<div class="btn abs" style="top:2068px;left:280px;width:180px">READ MORE</div>
<div class="founder-photo abs" role="img" aria-label="Portrait photo of the firm's founder"></div>

<!-- insights -->
<span class="section-mark abs" style="top:2332px;background:var(--white)"></span>
<h2 class="section-title abs center" style="top:2365px;color:var(--white)">INSIGHTS</h2>
<p class="body-copy abs center" style="top:2412px;width:1200px;color:var(--white)">Aliquam molestie, mi et imperdiet euismod, dui purus auctor tellus, et interdum lacus lectus et ante.</p>
<article class="insight abs" style="left:76px"><h3>NAM FERMENTUM VESTIBULUM</h3><p class="date">Apr 11, 2018</p><p>Aliquam molestie, mi et imperdiet euismod, dui purus auctor tellus et interdum lacus lectus et ante.</p><a>Read More</a></article>
<article class="insight abs" style="left:435px"><h3>NAM FERMENTUM VESTIBULUM</h3><p class="date">Apr 11, 2018</p><p>Aliquam molestie, mi et imperdiet euismod, dui purus auctor tellus et interdum lacus lectus et ante.</p><a>Read More</a></article>
<article class="insight abs" style="left:795px"><h3>NAM FERMENTUM VESTIBULUM</h3><p class="date">Apr 11, 2018</p><p>Aliquam molestie, mi et imperdiet euismod, dui purus auctor tellus et interdum lacus lectus et ante.</p><a>Read More</a></article>

<!-- contact -->
<span class="section-mark abs" style="top:2918px"></span>
<h2 class="section-title abs center" style="top:2953px">CONTACT</h2>
<p class="abs center" style="top:3004px;width:1200px;color:var(--red);font-size:14.5px;font-weight:700">DANIEL HARTLEY</p>
<p class="contact-line abs" style="top:3032px"><svg viewBox="0 0 14 14"><path d="M7 0 C3 0 1 3 1 5.5 C1 9 7 14 7 14 C7 14 13 9 13 5.5 C13 3 11 0 7 0 Z M7 8 A2.5 2.5 0 1 1 7 3 A2.5 2.5 0 0 1 7 8 Z"/></svg>48 Linden Hill Road, Westport, CT 06880, U.S.A.</p>
<p class="contact-line abs" style="top:3060px"><svg viewBox="0 0 14 14"><path d="M3 0 L5.5 3.5 L4 5.5 C5 8 6 9 8.5 10 L10.5 8.5 L14 11 L12 14 C5 13 1 9 0 2 Z"/></svg>+1-555-014-2290</p>
<p class="contact-line abs" style="top:3088px"><svg viewBox="0 0 14 14"><path d="M0 2 H14 V12 H0 Z" /><path d="M0 2 L7 8 L14 2" fill="none" stroke="#fff" stroke-width="1.3"/></svg>daniel.hartley@bluefinchadvisorypartners.com</p>
<div class="btn abs" style="top:3150px;left:510px;width:180px">CONTACT US</div>

<!-- footer -->
<p class="copyright abs center">Copyright © 2018 Company Name. All Rights Reserved.</p>
<div class="social abs" aria-label="Social media links"><span></span><span></span><span></span><span></span><span></span></div>

</body>
</html>
```